Merrow Trade finance web design

We are a newly established business which provides invoice finance to Small Businesses in England and Wales.
Our approach is very much a funder where the small business owner can talk to the decision maker. We will guarantee on receipt of information, a decision within 24 hours.
We are not a bank so the look of the website need to be friendly but professional.
Have two types of people we are trying to attract to the website: 1) partners who are small business owners and 2) introducers who is accountants and commercial brokers who introduce us to the small businesses.
Currently no website, although domain has been reserved.
The design should be:
Professional
“Clean” Look
Designed to convey Trust and Authority.
Appeal to the small business owner.
Must incorporate:
Logo (attached)
Front page:Top tabs to other pages 1) About us 2) Services 3) Introducers 4) Contact us
Need picture and logo on page.
1) About us page- Room for talk about the company, the people and our critera.
2) Services page- We need for what invoice finance is, and 5 boxes for different services we will provide. (link on page to contact us)
3) Introducers page- We need a part for why become an introducer? Who we can help? Why we are different? (link on page to contact us)
4) Contact us page- Office address, email, tel and if possible a map and a contact me part which will email direct to us.
Text will be provided for the design, if we can see the setup of the website we will provide a part for each of the pages to support.
Styles we think convey the correct image:
www.dornelcapital.example
www.plivanlend.example
www.quorbacredit.example
Target Market(s)
Small business owners
Industry/Entity Type
Finance
Number of Pages Required
5+ page
Look and feel

```html
<!DOCTYPE html>
<html lang="en">
<head>
<meta charset="utf-8">
<title>Merrow Trade finance</title>
<link rel="stylesheet" href="https://fonts.googleapis.com/css2?family=Roboto:wght@300;400;500;700&family=Arimo:wght@400&display=swap">
<style>
:root{
  --red:#e5373c;
  --red-dark:#d42f34;
  --ink:#2b2b2b;
  --body:#8a8a8a;
  --grey-bg:#eeeeee;
  --white:#ffffff;
}
*{box-sizing:border-box;margin:0;padding:0}
html,body{width:1200px;height:3651px;overflow:hidden;background:var(--white)}
body{position:relative;font-family:"Roboto",sans-serif;color:var(--ink)}
.abs{position:absolute}
.btn{position:absolute;display:flex;align-items:center;justify-content:center;background:var(--red);color:var(--white);border-radius:30px;font:400 20px "Roboto",sans-serif;text-transform:uppercase}
.lorem{font-family:"Arimo",sans-serif;color:var(--body);font-size:14px;line-height:27px}
.accent{color:var(--red)}

/* header */
.site-header{position:absolute;left:0;top:0;width:1200px;height:127px;background:var(--white);border-bottom:4px solid var(--red)}
.brand{position:absolute;left:78px;top:26px;display:flex;align-items:center;gap:14px}
.brand-dot{width:22px;height:22px;background:var(--red);border-radius:50%}
.brand-name{font:500 34px "Roboto",sans-serif;color:var(--red)}
.phone{position:absolute;left:928px;top:11px;display:flex;align-items:center;gap:18px;font:400 22px "Roboto",sans-serif;color:var(--ink)}
.phone-icon{width:52px;height:52px;border-radius:50%;background:var(--red);display:flex;align-items:center;justify-content:center}
.main-nav a{position:absolute;top:70px;height:44px;line-height:44px;font:400 16px/44px "Roboto",sans-serif;color:var(--ink);text-decoration:none;text-transform:uppercase}
.main-nav .current{background:var(--red);color:var(--white);border-radius:22px;width:100px;text-align:center}

/* hero */
.hero{position:absolute;left:0;top:127px;width:1200px;height:554px;background:linear-gradient(100deg,#6d7a86 0%,#c9cdd2 35%,#e3e6ea 55%,#b9bec4 80%,#9aa0a6 100%)}
.hero-title{position:absolute;right:83px;top:183px;font:400 48px "Roboto",sans-serif;color:var(--ink)}
.hero-text{position:absolute;right:83px;top:252px;width:620px;text-align:right;font:400 14px/27px "Arimo",sans-serif;color:#222}
.hero .btn{left:859px;top:350px;width:263px;height:63px}

/* welcome */
.welcome{position:absolute;left:0;top:681px;width:1200px;height:239px;background:var(--red);text-align:center;color:var(--white)}
.welcome h1{margin-top:42px;font:400 44px "Roboto",sans-serif;color:var(--ink)}
.welcome h1 span{color:var(--white)}
.welcome p{width:1000px;margin:12px auto 0;font:400 14px/27px "Arimo",sans-serif}
.welcome svg{margin-top:4px}

/* services */
.service{position:absolute;left:0;width:1200px;height:343px}
.service.alt{background:var(--grey-bg)}
.service h2{position:absolute;top:52px;font:400 32px "Roboto",sans-serif;text-transform:uppercase}
.service .lorem{position:absolute;top:98px;width:620px}
.service .btn{top:225px;width:165px;height:58px}
.service-art{position:absolute;top:30px;width:370px;height:280px;border-radius:6px}

/* contact band */
.contact-band{position:absolute;left:0;top:2636px;width:1200px;height:400px}
.contact-band h2{position:absolute;top:62px;width:1200px;text-align:center;font:400 38px "Roboto",sans-serif;color:var(--ink)}
.contact-band h2 span{color:var(--white)}
.contact-band .sub{position:absolute;top:118px;width:1200px;text-align:center;font:400 14px "Arimo",sans-serif;color:#2b2b2b}
.contact-band .ask{position:absolute;top:146px;width:1200px;text-align:center;font:400 27px "Roboto",sans-serif;color:var(--white)}
.field{position:absolute;top:212px;height:49px;background:var(--white);font:400 16px/49px "Arimo",sans-serif;color:#555;padding-left:16px}
.submit{position:absolute;left:908px;top:212px;width:168px;height:49px;border:2px solid var(--white);color:var(--white);font:400 20px/45px "Roboto",sans-serif;text-align:center}

/* introducers */
.introducers h2{position:absolute;top:3055px;width:1200px;text-align:center;font:400 40px "Roboto",sans-serif}
.intro-col{position:absolute;top:3138px;width:340px}
.intro-col h3{font:400 18px "Roboto",sans-serif;text-transform:uppercase;margin-bottom:12px}
.intro-col .btn{position:absolute;top:185px;left:0;width:178px;height:58px}

/* footer */
.site-footer{position:absolute;left:0;top:3442px;width:1200px;height:209px;background:var(--red);color:var(--white)}
.foot-nav a{position:absolute;top:19px;height:44px;font:400 15px/44px "Roboto",sans-serif;color:var(--white);text-decoration:none}
.foot-nav .current{border:2px solid var(--white);border-radius:22px;width:100px;text-align:center;line-height:40px}
.social{position:absolute;top:17px;width:48px;height:48px;border-radius:50%;border:2px solid var(--white)}
.social.fill{background:var(--white)}
.foot-rule{position:absolute;left:78px;top:83px;width:1044px;height:1px;background:rgba(255,255,255,.45)}
.foot-title{position:absolute;left:78px;top:98px;font:400 18px "Roboto",sans-serif;text-transform:uppercase}
.foot-icon{position:absolute;top:132px;width:48px;height:48px;border-radius:50%;background:var(--white);display:flex;align-items:center;justify-content:center}
.foot-text{position:absolute;font:400 15px/22px "Arimo",sans-serif}
</style>
</head>
<body>

<header class="site-header">
  <div class="brand"><span class="brand-dot"></span><span class="brand-name">Merrow Trade finance</span></div>
  <div class="phone">
    <span class="phone-icon"><svg width="24" height="24" viewBox="0 0 24 24"><path fill="#fff" d="M6.6 10.8a15 15 0 0 0 6.6 6.6l2.2-2.2c.3-.3.7-.4 1-.2 1.1.4 2.3.6 3.6.6.6 0 1 .4 1 1V20c0 .6-.4 1-1 1A17 17 0 0 1 3 4c0-.6.4-1 1-1h3.5c.6 0 1 .4 1 1 0 1.3.2 2.5.6 3.6.1.3 0 .7-.2 1z"/></svg></span>
    123 456 7890
  </div>
  <nav class="main-nav">
    <a class="current" style="left:475px">Home</a>
    <a style="left:616px">About Us</a>
    <a style="left:738px">Services</a>
    <a style="left:862px">Introducers</a>
    <a style="left:1017px">Contact Us</a>
  </nav>
</header>

<section class="hero" role="img" aria-label="Photo of two smiling business people in suits with colleagues in an office behind them">
  <h1 class="hero-title">Business Finance Limited</h1>
  <p class="hero-text">Lorem Ipsum is simply dummy text of the printing and typesetting industry. Lorem Ipsum has been the industry's standard dummy text ever since the when an unknown printer took a galley of type and scrambled it to make a specimen book.</p>
  <span class="btn">Contact Us Know</span>
</section>

<section class="welcome">
  <h1>WELCOME TO <span>MERROW</span></h1>
  <p>Lorem Ipsum is simply dummy text of the printing and typesetting industry. Lorem Ipsum has been the industry's standard dummy text ever since the 1500s, when an unknown printer took a galley of type and scrambled it to make a type specimen book. It has survived not only five centuries. Lorem Ipsum is simply dummy text of the printing and typesetting industry.</p>
  <svg width="20" height="20" viewBox="0 0 20 20"><path d="M4 4l6 6 6-6M4 10l6 6 6-6" fill="none" stroke="#fff" stroke-width="2"/></svg>
</section>

<section class="service" style="top:920px">
  <div class="service-art" style="left:73px;background:linear-gradient(90deg,#c9a24a,#e8e1cf 60%,#f4f4f4)" role="img" aria-label="Illustration of a young plant growing on stacks of coins"></div>
  <h2 style="left:494px">Services <span class="accent">One</span></h2>
  <p class="lorem" style="left:494px">Lorem Ipsum is simply dummy text of the printing and typesetting industry. Lorem Ipsum has been the industry's standard dummy text ever since the 1500s, when an unknown printer took a galley of type and scrambled it to make a type specimen book. It has survived not only five centuries. Lorem Ipsum is simply dummy text of the printing and typesetting industry.</p>
  <span class="btn" style="left:498px">Know More</span>
</section>

<section class="service alt" style="top:1263px">
  <h2 style="left:78px">Services <span class="accent">Two</span></h2>
  <p class="lorem" style="left:78px">Lorem Ipsum is simply dummy text of the printing and typesetting industry. Lorem Ipsum has been the industry's standard dummy text ever since the 1500s, when an unknown printer took a galley of type and scrambled it to make a type specimen book. It has survived not only five centuries. Lorem Ipsum is simply dummy text of the printing and typesetting industry.</p>
  <span class="btn" style="left:80px">Know More</span>
  <div class="service-art" style="left:755px;top:50px;height:240px;background:linear-gradient(180deg,#f7f7f7,#e2e6e2)" role="img" aria-label="Screenshot of a finance dashboard with a bar chart and data table"></div>
</section>

<section class="service" style="top:1606px">
  <div class="service-art" style="left:73px;background:linear-gradient(135deg,#dce6ee,#f6f8fa 60%,#e9eef2)" role="img" aria-label="Illustration of business icons connected around a computer screen"></div>
  <h2 style="left:494px">Services <span class="accent">Three</span></h2>
  <p class="lorem" style="left:494px">Lorem Ipsum is simply dummy text of the printing and typesetting industry. Lorem Ipsum has been the industry's standard dummy text ever since the 1500s, when an unknown printer took a galley of type and scrambled it to make a type specimen book. It has survived not only five centuries. Lorem Ipsum is simply dummy text of the printing and typesetting industry.</p>
  <span class="btn" style="left:498px">Know More</span>
</section>

<section class="service alt" style="top:1950px">
  <h2 style="left:78px">Services <span class="accent">Four</span></h2>
  <p class="lorem" style="left:78px">Lorem Ipsum is simply dummy text of the printing and typesetting industry. Lorem Ipsum has been the industry's standard dummy text ever since the 1500s, when an unknown printer took a galley of type and scrambled it to make a type specimen book. It has survived not only five centuries. Lorem Ipsum is simply dummy text of the printing and typesetting industry.</p>
  <span class="btn" style="left:80px">Know More</span>
  <div class="service-art" style="left:770px;background:linear-gradient(160deg,#e4d85a,#8fb7d8 45%,#2c2c2c 100%)" role="img" aria-label="Illustration of a tablet showing a spreadsheet with 3D bar and pie charts"></div>
</section>

<section class="service" style="top:2292px">
  <div class="service-art" style="left:100px;background:linear-gradient(135deg,#b9d3ea,#f0e6c4 55%,#d7a640)" role="img" aria-label="Illustration of a coin jar with a magnifying glass, pencil and documents"></div>
  <h2 style="left:494px">Services <span class="accent">Five</span></h2>
  <p class="lorem" style="left:494px">Lorem Ipsum is simply dummy text of the printing and typesetting industry. Lorem Ipsum has been the industry's standard dummy text ever since the 1500s, when an unknown printer took a galley of type and scrambled it to make a type specimen book. It has survived not only five centuries. Lorem Ipsum is simply dummy text of the printing and typesetting industry.</p>
  <span class="btn" style="left:498px">Know More</span>
</section>

<section class="contact-band">
  <svg class="abs" style="left:0;top:0" width="1200" height="400" viewBox="0 0 1200 400"><polygon points="0,0 1200,0 1200,310 0,400" fill="#e5373c"/></svg>
  <h2>GET IN <span>TOUCH</span></h2>
  <p class="sub">Lorem Ipsum is simply dummy text of the printing and typesetting industry.</p>
  <p class="ask">Need a free quote, or have a question? Get in touch!</p>
  <div class="field" style="left:117px;width:253px">Name*</div>
  <div class="field" style="left:385px;width:253px">Email*</div>
  <div class="field" style="left:645px;width:253px">Phone*</div>
  <div class="submit">SUBMIT</div>
</section>

<section class="introducers">
  <h2>OUR <span class="accent">INTRODUCERS</span></h2>
  <div class="intro-col" style="left:78px">
    <h3>Why become an introducer ?</h3>
    <p class="lorem">Lorem Ipsum is simply dummy text of the printing and typesetting industry. Lorem Ipsum has been the industry's standard dummy text ever since the when an unknown printer took a galley of type and scrambled it to make a specimen book.</p>
    <span class="btn">Contact Us</span>
  </div>
  <div class="intro-col" style="left:435px">
    <h3>Who we help ?</h3>
    <p class="lorem">Lorem Ipsum is simply dummy text of the printing and typesetting industry. Lorem Ipsum has been the industry's standard dummy text ever since the when an unknown printer took a galley of type and scrambled it to make a specimen book.</p>
    <span class="btn">Contact Us</span>
  </div>
  <div class="intro-col" style="left:791px">
    <h3>Why we are different ?</h3>
    <p class="lorem">Lorem Ipsum is simply dummy text of the printing and typesetting industry. Lorem Ipsum has been the industry's standard dummy text ever since the when an unknown printer took a galley of type and scrambled it to make a specimen book.</p>
    <span class="btn">Contact Us</span>
  </div>
</section>

<footer class="site-footer">
  <nav class="foot-nav">
    <a class="current" style="left:78px">Home</a>
    <a style="left:207px">About Us</a>
    <a style="left:309px">Services</a>
    <a style="left:406px">Introducers</a>
    <a style="left:516px">Contact Us</a>
  </nav>
  <span class="social fill" style="left:964px"></span>
  <span class="social" style="left:1020px"></span>
  <span class="social" style="left:1076px"></span>
  <div class="foot-rule"></div>
  <div class="foot-title">Get in Toch</div>
  <span class="foot-icon" style="left:78px"><svg width="22" height="22" viewBox="0 0 24 24"><path fill="#e5373c" d="M12 2a7 7 0 0 0-7 7c0 5 7 13 7 13s7-8 7-13a7 7 0 0 0-7-7zm0 9.5A2.5 2.5 0 1 1 12 6.5a2.5 2.5 0 0 1 0 5z"/></svg></span>
  <p class="foot-text" style="left:144px;top:135px;width:180px">101 - Lorem ipsum is the simple dummy text.</p>
  <span class="foot-icon" style="left:346px;background:none;border:2px solid #fff"><svg width="22" height="22" viewBox="0 0 24 24"><path fill="#fff" d="M6.6 10.8a15 15 0 0 0 6.6 6.6l2.2-2.2c.3-.3.7-.4 1-.2 1.1.4 2.3.6 3.6.6.6 0 1 .4 1 1V20c0 .6-.4 1-1 1A17 17 0 0 1 3 4c0-.6.4-1 1-1h3.5c.6 0 1 .4 1 1 0 1.3.2 2.5.6 3.6.1.3 0 .7-.2 1z"/></svg></span>
  <p class="foot-text" style="left:409px;top:145px">123 456 7890</p>
  <span class="foot-icon" style="left:606px;background:none;border:2px solid #fff"><svg width="22" height="22" viewBox="0 0 24 24"><path fill="#fff" d="M3 5h18v14H3zm2 2v.5l7 4.5 7-4.5V7l-7 4.5z"/></svg></span>
  <p class="foot-text" style="left:674px;top:145px">info@merrowtrade.example</p>
  <p class="foot-text" style="left:876px;top:135px;width:240px">© 2016 MERROW - All rights reserved.</p>
</footer>

</body>
</html>
```